Personal training and nutrition business needs business card design

We need a business card that outlays our services and invites potential customers to join our team and take the first step to a healthier and more enjoyable life. We cater for any level of fitness and specialize in weight loss and conditioning, strength training, muscle gain and strength endurance. Whether you are just starting off or need some help getting to the next level of your journey we are here to get the job done.
We specialize in one on one or one on two personal training sessions and each program will be custom made to suit individual fitness goals of our clients

```html
<!DOCTYPE html>
<html lang="en">
<head>
<meta charset="utf-8">
<title>Stride &amp; Steady business card</title>
<link href="https://fonts.googleapis.com/css2?family=Exo+2:ital,wght@1,800&family=Oswald:wght@500&family=Roboto:wght@400;700;900&display=swap" rel="stylesheet">
<style>
  :root {
    --backdrop: #2b2b2b;
    --card: #eeeeee;
    --ink: #111111;
    --text: #2a2a2a;
    --purple: #7a45a0;
    --violet: #6a3e9e;
    --magenta: #a2559b;
  }
  * { margin: 0; padding: 0; box-sizing: border-box; }
  html, body { width: 1200px; height: 1138px; overflow: hidden; background: var(--backdrop); }
  body { position: relative; font-family: "Roboto", sans-serif; }

  .card {
    position: absolute;
    background: linear-gradient(180deg, #f3f3f3 0%, #e6e6e6 100%);
    border-radius: 16px;
    overflow: hidden;
    box-shadow: 0 6px 14px rgba(0,0,0,.45);
  }
  .card-front { left: 274px; top: 186px; width: 623px; height: 376px; }
  .card-back  { left: 276px; top: 608px; width: 618px; height: 374px; }

  /* front */
  .front-brand {
    position: absolute; left: 0; right: 0; top: 168px;
    display: flex; justify-content: center; align-items: center; gap: 16px;
  }
  .brand-dot { width: 30px; height: 30px; border-radius: 50%; background: var(--purple); }
  .brand-name {
    font-family: "Roboto", sans-serif; font-weight: 900;
    font-size: 44px; letter-spacing: 1px; color: var(--ink); text-transform: uppercase;
  }
  .tagline {
    font-family: "Oswald", sans-serif; font-weight: 500; color: var(--purple);
    text-transform: uppercase; letter-spacing: 1.6px;
  }
  .front-tagline { position: absolute; left: 0; right: 0; top: 252px; text-align: center; font-size: 14px; }
  .front-web {
    position: absolute; left: 0; right: 0; top: 322px;
    display: flex; justify-content: center; align-items: center; gap: 18px;
    font-size: 16px; color: var(--ink);
  }
  .rule { width: 72px; height: 2px; background: var(--ink); border-radius: 2px; }
  .front-band {
    position: absolute; left: 0; right: 0; bottom: 0; height: 9px;
    background: linear-gradient(90deg, var(--magenta), var(--violet));
  }

  /* back */
  .back-brand { position: absolute; left: 26px; top: 52px; display: flex; align-items: center; gap: 14px; }
  .back-brand .brand-dot { width: 26px; height: 26px; }
  .back-brand .brand-name { font-size: 30px; line-height: 1; }
  .back-tagline { position: absolute; left: 66px; top: 92px; font-size: 9px; letter-spacing: 1px; }

  .person-name {
    position: absolute; left: 44px; top: 204px;
    font-family: "Exo 2", sans-serif; font-style: italic; font-weight: 800;
    font-size: 25px; letter-spacing: 1px; color: var(--purple); text-transform: uppercase;
  }
  .person-role { position: absolute; left: 42px; top: 238px; font-size: 16px; color: var(--text); }
  .divider { position: absolute; left: 0; top: 0; }
  .address { position: absolute; left: 42px; top: 292px; font-size: 16px; line-height: 24px; color: var(--text); }
  .contacts { position: absolute; right: 42px; top: 266px; list-style: none; }
  .contacts li {
    display: flex; justify-content: flex-end; align-items: center; gap: 12px;
    font-size: 16px; line-height: 24px; color: var(--text);
  }
  .contacts svg { width: 14px; height: 14px; fill: var(--purple); }
</style>
</head>
<body>

<section class="card card-front">
  <div class="front-brand">
    <span class="brand-dot"></span>
    <span class="brand-name">Stride &amp; Steady</span>
  </div>
  <p class="tagline front-tagline">Personal Training.&nbsp; Nutrition. Motivation</p>
  <div class="front-web">
    <span class="rule"></span>
    <span>www.stridesteady.com</span>
    <span class="rule"></span>
  </div>
  <div class="front-band"></div>
</section>

<section class="card card-back">
  <div class="back-brand">
    <span class="brand-dot"></span>
    <span class="brand-name">Stride &amp; Steady</span>
  </div>
  <p class="tagline back-tagline">Personal Training.&nbsp; Nutrition. Motivation</p>

  <h1 class="person-name">Sam Rivers</h1>
  <p class="person-role">Personal Trainer</p>

  <svg class="divider" width="618" height="374" viewBox="0 0 618 374" aria-hidden="true">
    <path d="M42 275 H318 C345 275 350 243 380 243 H576" fill="none" stroke="#7a45a0" stroke-width="1.6"/>
  </svg>

  <p class="address">1820 Cedar Bend Lane<br>Maple Grove TX 75000</p>

  <ul class="contacts">
    <li>+1 (555) 014-2270
      <svg viewBox="0 0 16 16" aria-hidden="true"><path d="M2 5c0-2 3-3 6-3s6 1 6 3v1h-3V5H5v1H2zM4 7h8l2 6H2z"/></svg>
    </li>
    <li>sam@stridesteady.com
      <svg viewBox="0 0 16 16" aria-hidden="true"><path d="M1 3h14v10H1zM2 4l6 5 6-5v-.1H2z" fill-rule="evenodd"/></svg>
    </li>
    <li>www.stridesteady.com
      <svg viewBox="0 0 16 16" aria-hidden="true"><circle cx="8" cy="8" r="7"/></svg>
    </li>
  </ul>
</section>

</body>
</html>
```